Debt Collection Website Design! We are the solution for landlords to get paid what they are owed.

We are a 3rd party debt collection company that specializes in Residential and Commercial real estate debt collection. We help landlords recover money from past residents by being fair, friendly and aggressive. We also collect/buy/sell/trade civil judgments won resulting from anything from automobile accidents to evictions to a pet zebra getting stolen. We buy single judgments to large portfolios, we also collect judgments for a nominal fee.

I would like a new, modern, easy to navigate website. A spot that we can post news stories or updated information about our company. I have included our company logo that must be on the top of the page. Feel free to ask any questions that will help get the process going.

Target Market(s)

Landlords, small to large apartment complex. Real estate services and lawyers.

Industry/Entity Type

Real Estate

Number of Pages Required

3 page

Requirements
Must have
• Company logo which has been attached. A page where we can explain the collection process, fees and placement. A page where we can explain judgments, collection vs. selling, placement form. I am open to any font/designs and willing to work with anyone.
Nice to have
• Nice to have a spot on the homepage to place news articles about ourselves and our industry.
Should not have
• I don't want it over crowded. Simple, sleek and easy to navigate is best. No gavels on any of the pages. It cannot look legal, say/show anything that we use legal powers to collect. We are not a law office, we don't practice law, we are 3rd party debt collection agency.

```html
<!DOCTYPE html>
<html lang="en">
<head>
<meta charset="utf-8">
<title>Halvern Recovery, LLC</title>
<link href="https://fonts.googleapis.com/css2?family=Titillium+Web:wght@400;600;700&family=Open+Sans:wght@400;600;700&display=swap" rel="stylesheet">
<style>
:root{
  --navy:#0f3a84;
  --navy-dark:#0d2f6e;
  --grey:#9aa3ab;
  --band:#ececec;
  --text:#555;
  --white:#fff;
  --line:#c9c9c9;
}
*{margin:0;padding:0;box-sizing:border-box}
html,body{width:698px;height:1200px;overflow:hidden;background:var(--white)}
body{position:relative;font-family:"Open Sans",sans-serif;color:var(--text)}
.abs{position:absolute}
.top-rule{left:0;top:0;width:698px;height:3px;background:var(--navy)}
.brand{left:66px;top:20px;display:flex;align-items:center;gap:8px;height:38px}
.brand-mark{width:30px;height:30px;background:var(--navy)}
.brand-name{font-family:"Titillium Web",sans-serif;font-weight:600;font-size:19px;color:var(--navy);line-height:1;letter-spacing:.5px}
.search{left:510px;top:25px;width:120px;height:21px;border:1px solid #cfcfcf;font-size:8px;color:#333;padding:5px 6px;}
.search svg{position:absolute;right:5px;top:4px}
.nav{left:66px;top:70px;width:564px;height:37px;display:flex;font-family:"Titillium Web",sans-serif;font-weight:600;font-size:8.5px;color:var(--white)}
.nav a{color:inherit;text-decoration:none;display:flex;align-items:center;justify-content:center}
.nav .home{width:71px;background:var(--grey)}
.nav .main{width:350px;background:var(--navy);display:flex;justify-content:space-around;padding:0 10px}
.nav .social{flex:1;background:var(--grey);display:flex;align-items:center;justify-content:center;gap:16px}
.nav .social span{width:9px;height:9px;border-radius:50%;background:#dfe3e6}
.slider{left:66px;top:118px;width:565px;height:295px;border:1px solid #ddd;box-shadow:0 4px 6px rgba(0,0,0,.18);background:var(--white)}
.slide-photo{left:5px;top:5px;width:554px;height:283px;background:linear-gradient(135deg,#a57b55 0%,#c7b596 40%,#d8dbe0 65%,#3f5f8f 100%)}
.arrow{width:16px;height:16px;border-radius:50%;background:rgba(255,255,255,.9);display:flex;align-items:center;justify-content:center}
.dots-tab{left:236px;top:273px;width:82px;height:16px;background:var(--white);border-radius:40px 40px 0 0;display:flex;gap:5px;justify-content:center;align-items:center}
.dot{width:7px;height:7px;border-radius:50%;border:1px solid var(--navy)}
.dot.on{background:var(--navy)}
h2{font-family:"Titillium Web",sans-serif;font-weight:600;color:var(--navy);line-height:1}
.welcome h2{font-size:18px}
.welcome{left:66px;top:434px;width:362px}
.welcome p{margin-top:10px;font-size:6.6px;line-height:14px}
.welcome-photo{left:434px;top:431px;width:196px;height:147px;background:linear-gradient(135deg,#d8dee6,#7fa9d6 60%,#2c5aa0);border:1px solid #ccc}
.projects-band{left:0;top:605px;width:698px;height:236px;background:var(--band)}
.projects-title{left:66px;top:627px;font-size:18px}
.card{width:180px}
.card .ph{height:72px;border:2px solid var(--white);box-shadow:0 0 2px rgba(0,0,0,.3)}
.card h3{margin-top:12px;font-family:"Titillium Web",sans-serif;font-weight:600;font-size:10px;color:#222;padding-left:2px}
.card p{font-size:7px;line-height:14px;padding-left:2px;margin-top:2px}
.btn{display:inline-flex;align-items:center;justify-content:center;background:var(--navy);color:var(--white);font-family:"Titillium Web",sans-serif;font-weight:700;font-size:7.5px;border-radius:2px}
.card .btn{margin-top:10px;width:73px;height:21px}
.video{left:456px;top:636px;width:174px;height:174px;border-radius:3px;background:linear-gradient(160deg,#5d6268,#3d4146 60%,#2b2e33);display:flex;flex-direction:column;align-items:center;justify-content:center;color:var(--white)}
.video .play{width:20px;height:20px;border:1.5px solid var(--white);border-radius:50%;display:flex;align-items:center;justify-content:center;margin-top:8px}
.video h3{font-family:"Titillium Web",sans-serif;font-weight:700;font-size:14px;margin-top:16px}
.news-title{left:65px;top:863px;font-size:14px}
.news{left:65px;top:886px;width:564px;height:103px;display:flex}
.news .col{width:141px;height:103px}
.news .txt{padding:9px 8px;color:var(--white)}
.news .txt h3{font-family:"Titillium Web",sans-serif;font-weight:600;font-size:11px;line-height:1}
.news .txt p{font-size:6.4px;font-weight:600;line-height:11px;margin-top:4px}
.partners-title{left:66px;top:1022px;font-size:14px}
.partners-rule{left:126px;top:1031px;width:248px;height:1px;background:var(--line)}
.partners-dots{left:377px;top:1028px;display:flex;gap:3px}
.partners-dots .dot{width:6px;height:6px}
.partners-row{left:66px;top:1056px;width:340px;height:28px;display:flex;justify-content:space-between}
.badge{width:70px;height:26px;border-radius:3px;background:#d9dce2}
.qc-title{left:430px;top:1022px;font-size:14px}
.qc-text{left:430px;top:1047px;width:190px;font-size:7px;line-height:11.5px;color:#444}
.qc-btn{left:558px;top:1087px;width:72px;height:21px}
.footer{left:0;top:1126px;width:698px;height:74px;background:var(--navy);color:var(--white)}
.footer-links{left:67px;top:18px;font-family:"Titillium Web",sans-serif;font-size:10px}
.footer-links span{margin:0 4px}
.footer-copy{left:67px;top:38px;font-size:6.5px}
.footer-social{left:560px;top:26px;display:flex;gap:5px}
.footer-social span{width:13px;height:13px;background:#dfe6f2;border-radius:2px}
</style>
</head>
<body>
<div class="abs top-rule"></div>

<header>
  <div class="abs brand"><span class="brand-mark"></span><span class="brand-name">HALVERN RECOVERY, LLC</span></div>
  <div class="abs search">Search
    <svg width="11" height="11" viewBox="0 0 12 12"><circle cx="5" cy="5" r="3.8" fill="none" stroke="#111" stroke-width="1.6"/><line x1="7.8" y1="7.8" x2="11" y2="11" stroke="#111" stroke-width="1.8"/></svg>
  </div>
  <nav class="abs nav">
    <a class="home" href="#">Home</a>
    <div class="main"><a href="#">Strategy</a><a href="#">People</a><a href="#">Blog</a><a href="#">Contact us</a></div>
    <div class="social"><span></span><span></span><span></span><span></span></div>
  </nav>
</header>

<section class="abs slider">
  <div class="abs slide-photo" role="img" aria-label="Desk with calculator, glasses and a person filling in a form"></div>
  <div class="abs arrow" style="left:22px;top:135px"><svg width="6" height="8" viewBox="0 0 6 8"><path d="M5 1 2 4l3 3" fill="none" stroke="#333" stroke-width="1.4"/></svg></div>
  <div class="abs arrow" style="left:524px;top:135px"><svg width="6" height="8" viewBox="0 0 6 8"><path d="M1 1l3 3-3 3" fill="none" stroke="#333" stroke-width="1.4"/></svg></div>
  <div class="abs dots-tab"><span class="dot on"></span><span class="dot"></span><span class="dot"></span></div>
</section>

<section class="abs welcome">
  <h2>Welcome To Halvern</h2>
  <p>Lorem ipsum dolor sit amet, consectetuer adipiscing elit, sed diam nonummy nibh euismod tincidunt ut laoreet dolore magna aliquam erat volutpat. Ut wisi enim ad minim veniam, quis nostrud exerci tation ullamcorper suscipit lobortis nisl ut aliquip ex ea commodo consequat. Lorem ipsum dolor sit amet, consectetuer adipiscing elit, sed diam nonummy nibh euismod tincidunt ut laoreet dolore magna aliquam erat volutpat. Ut wisi enim ad minim veniam, quis nostrud exerci tation ullamcorper suscipit lobortis nisl ut aliquip ex ea commodo consequat. Lorem ipsum dolor sit amet, consectetuer adipiscing elit, sed diam nonummy nibh euismod tincidunt ut laoreet dolore magna aliquam erat volutpat. Ut wisi enim ad minim veniam, quis nostrud exerci tation ullamcorper suscipit lobortis nisl ut aliquip ex ea commodo consequat. Lorem ipsum dolor sit amet,</p>
</section>
<div class="abs welcome-photo" role="img" aria-label="Hands holding a clipboard with bar charts"></div>

<section class="abs projects-band"></section>
<h2 class="abs projects-title">Our Projects</h2>
<article class="abs card" style="left:66px;top:658px">
  <div class="ph" role="img" aria-label="Suburban family house" style="background:linear-gradient(180deg,#4a86d0 0%,#9cc0e6 45%,#e2d8c4 60%,#6d8a4a 100%)"></div>
  <h3>Residential</h3>
  <p>Vivamus porttitor g puttrus nisi eleifend libero a tempus libero lectus feugiat felis Morbi diam</p>
  <a class="btn" href="#">READ MORE</a>
</article>
<article class="abs card" style="left:256px;top:658px">
  <div class="ph" role="img" aria-label="Commercial storefront building" style="background:linear-gradient(180deg,#6f97cf 0%,#c9ccc8 40%,#9c9b92 75%,#6b6a66 100%)"></div>
  <h3>Commercial</h3>
  <p>Vivamus porttitor g puttrus nisi eleifend libero a tempus libero lectus feugiat felis Morbi diam</p>
  <a class="btn" href="#">READ MORE</a>
</article>
<div class="abs video" role="img" aria-label="Video: stressed driver after a car accident">
  <span class="play"><svg width="7" height="8" viewBox="0 0 7 8"><path d="M1 0.5 6.5 4 1 7.5z" fill="#fff"/></svg></span>
  <h3>Automobile Accidents</h3>
</div>

<h2 class="abs news-title">Latest News</h2>
<section class="abs news">
  <div class="col txt" style="background:var(--navy)"><h3>lorem ipsum</h3><p>Lorem ipsum dolor sit amet, consectetuer adipiscing elit, sed diam nonummy nibh euismod tincidunt ut laoreet dolore magna aliquam erat volutpat.<br>Read more..</p></div>
  <div class="col" role="img" aria-label="House porch with red door" style="background:linear-gradient(135deg,#5a4a40,#8a6f5c 50%,#b9b6a8)"></div>
  <div class="col txt" style="background:var(--grey)"><h3>lorem ipsum</h3><p>Lorem ipsum dolor sit amet, consectetuer adipiscing elit, sed diam nonummy nibh euismod tincidunt ut laoreet dolore magna aliquam erat volutpat.<br>Read more..</p></div>
  <div class="col" role="img" aria-label="White wall with window and dark green door" style="background:linear-gradient(180deg,#d9d7d2,#c4c2bc 75%,#4a4a48)"></div>
</section>

<h2 class="abs partners-title">Partners</h2>
<div class="abs partners-rule"></div>
<div class="abs partners-dots"><span class="dot on"></span><span class="dot"></span><span class="dot"></span></div>
<div class="abs partners-row"><span class="badge"></span><span class="badge"></span><span class="badge"></span><span class="badge"></span></div>

<h2 class="abs qc-title">Quick Contact</h2>
<p class="abs qc-text">Nunc tempus felis vitae urna Vivamus porttitor g purus nisi eleifend libero a tempus libero lectus Nunc tempus felis vitae urna Vivamus</p>
<a class="abs btn qc-btn" href="#">CLICK HERE</a>

<footer class="abs footer">
  <div class="abs footer-links">Home<span>|</span>About Us<span>|</span>Serives<span>|</span>Contact Us<span>|</span>Blog</div>
  <div class="abs footer-copy">© 2014 Company Name&nbsp; All right reserved&nbsp; Term of Use</div>
  <div class="abs footer-social"><span></span><span></span><span></span><span></span></div>
</footer>
</body>
</html>
```